New Website for World Wide Charity (KOLVAN)

We need a dynamic web design for our brand new charity organisation that will be working worldwide. We will be funded by donations so need to attract people to donate.

What We Do
We work to optimise the wellbeing of the planet, the animals and all that live within. Our slogan is Achieving Vibrational Equilibrium.

We have included a Powerpoint document which may help you understand what we need, it is just an idea for structure and style, it is not set in stone so feel free to be as creative as you like!
Updates

Designs look the same

Target Market(s)

Adults 18+ with an interest in animal, environmental. Businesses that may like to support our natural world or already support our natural world.

Number of Pages Required

3 page

Colors

Designer to choose colors to be used in the design.

Requirements
Must have
• We need the website to be easy to use and understand.

Web pages will be Home, What We Do, Who We Are, Success Stories, What You Can Do (Blog section), Seek Help, Donate, Join.
Nice to have
• Natural feel, easy to navigate, Ideally the website will look natural and organic.

Natural colours, blues, greens, sand, gold, brown, grey, silver, Orange and yellow for impact.
Should not have
• Should not have a dark coloured theme.

```html
<!DOCTYPE html>
<html lang="en">
<head>
<meta charset="utf-8">
<title>KOLVAN – Help Raise World Vibration</title>
<link href="https://fonts.googleapis.com/css2?family=Arimo:wght@400;700&display=swap" rel="stylesheet">
<style>
:root{
  --hero-a:#3d3fc9;
  --hero-b:#7a45b8;
  --hero-c:#c35ab0;
  --nav-bg:rgba(120,110,190,.55);
  --gold:#f5d20a;
  --white:#ffffff;
  --teal:#3c9ea8;
  --text:#333333;
  --env:#2f7d4a;
  --animal:#d98a22;
  --human:#4f9c8e;
  --btn-teal:#3ba3a8;
  --cta-text:#2f2fd8;
  --foot-a:#3d4af0;
  --foot-b:#8c55f0;
  --foot-c:#f258e0;
  --foot-bar:#1f1fd6;
}
*{margin:0;padding:0;box-sizing:border-box}
html,body{width:1200px;height:2572px;overflow:hidden;background:var(--white)}
body{font-family:"Arimo",Arial,sans-serif;color:var(--text);position:relative}
.hero{position:absolute;left:0;top:0;width:1200px;height:541px;
  background:linear-gradient(100deg,var(--hero-a) 0%,var(--hero-b) 55%,var(--hero-c) 100%)}
.topbar{position:absolute;left:0;top:0;width:1200px;height:88px;background:var(--nav-bg)}
.brand{position:absolute;left:152px;top:12px;display:flex;align-items:center;gap:8px}
.brand-mark{width:64px;height:64px;border-radius:50%;background:var(--white);display:flex;align-items:center;justify-content:center;font-size:11px;font-weight:700;color:var(--teal)}
.nav{position:absolute;right:150px;top:38px;display:flex;gap:33px;font-size:12px;color:var(--white)}
.nav .active{color:var(--gold)}
.hero-title{position:absolute;left:0;width:1200px;top:147px;text-align:center;color:var(--white);font-size:30px;font-weight:700;letter-spacing:.3px}
.hero-lede{position:absolute;left:350px;width:500px;top:206px;text-align:center;color:var(--white);font-size:14.5px;line-height:22.5px}
.cta{position:absolute;left:496px;top:326px;width:210px;height:42px;background:var(--white);color:var(--cta-text);font-size:13px;display:flex;align-items:center;justify-content:center}
.cards{position:absolute;left:150px;top:450px;width:900px;height:300px;display:flex}
.card{width:300px;height:300px;display:flex;flex-direction:column;align-items:center;justify-content:center;color:var(--white);text-align:center}
.card h3{font-size:21px;font-weight:700;letter-spacing:.5px}
.card-env{background:linear-gradient(180deg,#3a8a50,var(--env))}
.card-animal{background:linear-gradient(180deg,#d58a26,#e18a1e)}
.card-human{background:linear-gradient(160deg,#6aa8a0,var(--human))}
.card-animal p{font-size:12.5px;line-height:18px;width:210px;margin-top:18px}
.card-btn{margin-top:24px;width:162px;height:28px;background:var(--btn-teal);font-size:12px;display:flex;align-items:center;justify-content:center}
.photo{position:absolute;width:600px;height:450px}
.photo-env{left:0;top:833px;background:radial-gradient(circle at 50% 40%,#2e6a2c 0%,#1b2a1a 45%,#141a14 100%)}
.photo-animal{left:601px;top:1284px;background:radial-gradient(circle at 55% 55%,#c9a173 0%,#6f7d4a 45%,#57703f 100%)}
.photo-human{left:0;top:1734px;background:linear-gradient(120deg,#e9e4d3 0%,#9a8a5e 50%,#4f5a3a 100%)}
.divider{position:absolute;left:601px;top:1283px;width:599px;height:1px;background:var(--teal)}
.story{position:absolute;width:400px}
.story h2{color:var(--teal);font-size:25px;font-weight:700;letter-spacing:.3px;margin-bottom:20px}
.story p{font-size:14.5px;line-height:22.5px;margin-bottom:22px}
.story-env{left:652px;top:828px}
.story-animal{left:149px;top:1318px}
.story-human{left:652px;top:1778px}
.footer{position:absolute;left:0;top:2250px;width:1200px;height:302px;
  background:linear-gradient(100deg,var(--foot-a) 0%,var(--foot-b) 45%,var(--foot-c) 100%);color:var(--white)}
.fcol{position:absolute;top:70px;font-size:14px;font-weight:700}
.fcol h4{font-size:14px;font-weight:700;margin-bottom:38px}
.fcol li{list-style:none;font-weight:400;margin-bottom:14px;text-transform:uppercase}
.f1{left:188px}.f2{left:392px}.f3{left:577px}
.fbrand{position:absolute;left:860px;top:64px;width:68px;height:68px;border-radius:50%;background:var(--white);display:flex;align-items:center;justify-content:center;font-size:11px;font-weight:700;color:var(--teal)}
.fblurb{position:absolute;left:814px;top:146px;width:205px;font-size:13.5px;line-height:22.5px}
.bottombar{position:absolute;left:0;top:2552px;width:1200px;height:20px;background:var(--foot-bar);color:var(--white);font-size:13px}
.bottombar .copy{position:absolute;left:188px;top:2px}
.social{position:absolute;left:886px;top:2px;display:flex;gap:13px}
.social span{width:16px;height:16px;border-radius:50%;background:var(--white)}
</style>
</head>
<body>
<section class="hero" role="img" aria-label="Misty mountain forest with pine trees at sunrise, tinted purple"></section>
<header class="topbar">
  <div class="brand"><div class="brand-mark">KOLVAN</div></div>
  <nav class="nav">
    <span class="active">Home</span><span>What We Do</span><span>Who We Are</span><span>Success Stories</span><span>What You Can Do</span><span>Donate and Join.</span>
  </nav>
</header>
<h1 class="hero-title">HELP RAISE WORLD VIBRATION</h1>
<p class="hero-lede">Lorem ipsum dolor sit amet, consectetur adipiscing elit. Aenean ante eros, ullamcorper quis dignissim eget, volutpat interdum lectus. Sed interdum convallis dui et lobortis. Sed lobortis ex venenatis magna congue aliquam. Vivamus</p>
<a class="cta">MAKE A DIFFERENCE</a>

<div class="cards">
  <div class="card card-env" role="img" aria-label="Small potted tree, green tint"><h3>ENVIRONMENT</h3></div>
  <div class="card card-animal" role="img" aria-label="Two puppies in a flower field, orange tint">
    <h3>ANIMAL</h3>
    <p>tincidunt nulla nec malesuada accumsan. Fusce acinia, sapien ac suscipit ultricies, libero urna</p>
    <div class="card-btn">FIND OUT MORE</div>
  </div>
  <div class="card card-human" role="img" aria-label="Seated man resting with clasped hands, teal tint"><h3>HUMAN</h3></div>
</div>

<div class="photo photo-env" role="img" aria-label="Small round-crowned potted tree on a dark background"></div>
<article class="story story-env">
  <h2>ENVIRONMENT</h2>
  <p>mattis sapien, at iaculis ligula massa sit amet mauris. Sed a tincidunt arcu. Praesent massa dolor, finibus non cursus dapibus, ultrices a nisl. Cras maximus bibendum eros, non rutrum arcu bibendum nec. Etiam quis orci leo. Class aptent taciti sociosqu ad litora torquent per conubia nostra, per inceptos himenaeos. Pellentesque aliquet scelerisque risus sit amet lobortis.</p>
  <p>In lobortis, tortor et elementum laoreet, mi nibh gravida tortor, ac dapibus lacus augue at felis. Pellentesque pharetra in diam et sodales. Mauris nec velit eu velit mattis elementum ac in dui. Proin sit amet elit non nulla sodales faucibus. Donec ultricies vel justo nec accumsan. Nulla sollicitudin efficitur tempor. Lorem ipsum dolor sit amet, consectetur adipiscing elit. Curabitur egestas vehicula est, at molestie lectus condimentum non. Donec leo justo, eleifend sed nisl nec, scelerisque ultrices felis. Interdum et</p>
</article>

<div class="divider"></div>
<article class="story story-animal">
  <h2>ANIMAL</h2>
  <p>mattis sapien, at iaculis ligula massa sit amet mauris. Sed a tincidunt arcu. Praesent massa dolor, finibus non cursus dapibus, ultrices a nisl. Cras maximus bibendum eros, non rutrum arcu bibendum nec. Etiam quis orci leo. Class aptent taciti sociosqu ad litora torquent per conubia nostra, per inceptos himenaeos. Pellentesque aliquet scelerisque risus sit amet lobortis.</p>
  <p>In lobortis, tortor et elementum laoreet, mi nibh gravida tortor, ac dapibus lacus augue at felis. Pellentesque pharetra in diam et sodales. Mauris nec velit eu velit mattis elementum ac in dui. Proin sit amet elit non nulla sodales faucibus. Donec ultricies vel justo nec accumsan. Nulla sollicitudin efficitur tempor. Lorem ipsum dolor sit amet, malesuada fames ac ante ipsum primis in faucibus.</p>
</article>
<div class="photo photo-animal" role="img" aria-label="Two golden puppies sitting in grass among orange flowers"></div>

<div class="photo photo-human" role="img" aria-label="Man in a green jacket and cap sitting with head bowed and hands clasped"></div>
<article class="story story-human">
  <h2>HUMAN</h2>
  <p>mattis sapien, at iaculis ligula massa sit amet mauris. Sed a tincidunt arcu. Praesent massa dolor, finibus non cursus dapibus, ultrices a nisl. Cras maximus bibendum eros, non rutrum arcu bibendum nec. Etiam quis orci leo. Class aptent taciti sociosqu ad litora torquent per conubia nostra, per inceptos himenaeos. Pellentesque aliquet scelerisque risus sit amet lobortis.</p>
  <p>In lobortis, tortor et elementum laoreet, mi nibh gravida tortor, ac dapibus lacus augue at felis. Pellentesque pharetra in diam et sodales. Mauris nec velit eu velit mattis elementum ac in dui. Proin sit amet elit non nulla sodales faucibus. Donec ultricies vel justo nec accumsan. Nulla sollicitudin efficitur tempor. Lorem ipsum dolor sit amet,</p>
</article>

<footer class="footer">
  <div class="fcol f1"><h4>GET INVOLVED</h4><ul><li>Join us</li><li>Fundraise</li><li>Donate</li><li>Shop</li></ul></div>
  <div class="fcol f2"><h4>GET HELP</h4><ul><li>Contact us</li><li>Media</li></ul></div>
  <div class="fcol f3"><h4>LEGAL</h4><ul><li>Terms and conditions</li><li>Cookies</li><li>Privacy policy</li></ul></div>
  <div class="fbrand">KOLVAN</div>
  <p class="fblurb">Suspendisse ut suscipit tortor. Sed in risus turpis. Suspendisse cursus porta felis, sed aliquet ex ullamcorper id. Aliquam fringilla dolor vitae metus hendrerit, sollicitudin</p>
</footer>
<div class="bottombar">
  <span class="copy">© All Rights are Resereved</span>
  <div class="social"><span></span><span></span><span></span><span></span></div>
</div>
</body>
</html>
```